Corporate Business Card

Very professional, Modern, Not to busy, include phone address email, website
(253) 617-4930, 18761 52nd Avenue S, Ridgeford, NV 98047, martin@plumlinegroup.com, varkoworks.com

Target Market(s)

Manufacturing

Industry/Entity Type

Aero, machining, manufacturing, Off road racing

Contact Information for Business Card

Phone, address email, website

```html
<!DOCTYPE html>
<html lang="en">
<head>
<meta charset="utf-8">
<title>Varko Industries – Business Card</title>
<link href="https://fonts.googleapis.com/css2?family=Montserrat:wght@400;500;700;800&display=swap" rel="stylesheet">
<style>
  :root {
    --navy: #17366e;
    --red: #d0222b;
    --white: #ffffff;
    --ink: #111111;
    --canvas: #2b2b2b;
  }
  * { margin: 0; padding: 0; box-sizing: border-box; }
  html, body { width: 1200px; height: 1015px; overflow: hidden; }
  body {
    background: var(--canvas);
    font-family: "Montserrat", Arial, sans-serif;
    display: flex;
    flex-direction: column;
    align-items: center;
    justify-content: center;
    gap: 40px;
  }
  .card {
    position: relative;
    width: 780px;
    height: 446px;
    overflow: hidden;
    background: var(--navy);
    box-shadow: 0 10px 30px rgba(0,0,0,.45);
  }

  /* Brand block */
  .brand {
    position: absolute;
    left: 50%;
    transform: translateX(-50%);
    display: flex;
    flex-direction: column;
    align-items: center;
  }
  .brand-name {
    display: flex;
    align-items: center;
    gap: 16px;
    color: var(--white);
    font-weight: 800;
    font-size: 52px;
    letter-spacing: 1px;
    white-space: nowrap;
  }
  .brand-mark { width: 26px; height: 26px; background: var(--red); flex: none; }
  .brand-rule {
    margin-top: 18px;
    width: 300px;
    height: 2px;
    background: var(--white);
    align-self: flex-start;
  }

  /* Back side */
  .card--back .brand { top: 170px; }
  .edge-strip {
    position: absolute;
    left: 0; right: 0; bottom: 0;
    height: 16px;
    display: flex;
  }
  .edge-strip span { flex: 1; }
  .card--back .edge-strip span:first-child { background: var(--red); }
  .card--back .edge-strip span:last-child { background: var(--white); }

  /* Front side */
  .card--front .brand { top: 50px; }
  .card--front .brand-name { font-size: 44px; }
  .card--front .brand-rule { width: 250px; margin-top: 14px; }

  .info-band {
    position: absolute;
    left: 0; right: 0;
    top: 185px;
    height: 140px;
    background: var(--red);
    display: flex;
    align-items: center;
    color: var(--white);
  }
  .person { width: 330px; padding-left: 50px; }
  .person-name { font-weight: 800; font-size: 26px; letter-spacing: .5px; text-transform: uppercase; white-space: nowrap; }
  .person-title { font-weight: 500; font-size: 19px; margin-top: 2px; white-space: nowrap; }
  .divider { width: 2px; height: 80px; background: var(--white); margin: 0 26px 0 10px; flex: none; }
  .contacts { list-style: none; font-size: 17px; font-weight: 500; line-height: 1.55; white-space: nowrap; }
  .contacts li { display: flex; align-items: center; gap: 10px; }
  .contacts svg { width: 18px; height: 18px; flex: none; }

  .address-band {
    position: absolute;
    left: 0; right: 0;
    top: 325px;
    bottom: 16px;
    background: var(--white);
    display: flex;
    align-items: center;
    justify-content: center;
    color: var(--ink);
    font-size: 22px;
    font-weight: 500;
    white-space: nowrap;
  }
  .card--front .edge-strip span:first-child { background: var(--navy); }
  .card--front .edge-strip span:last-child { background: var(--red); }
</style>
</head>
<body>

  <section class="card card--back" aria-label="Business card, back">
    <div class="brand">
      <div class="brand-name"><span class="brand-mark"></span>Varko Industries</div>
      <div class="brand-rule"></div>
    </div>
    <div class="edge-strip"><span></span><span></span></div>
  </section>

  <section class="card card--front" aria-label="Business card, front">
    <div class="brand">
      <div class="brand-name"><span class="brand-mark"></span>Varko Industries</div>
      <div class="brand-rule"></div>
    </div>

    <div class="info-band">
      <div class="person">
        <div class="person-name">Daniel Harper</div>
        <div class="person-title">Managing Director</div>
      </div>
      <div class="divider"></div>
      <ul class="contacts">
        <li>
          <svg viewBox="0 0 24 24" fill="none" stroke="#fff" stroke-width="2.2" stroke-linecap="round" stroke-linejoin="round"><path d="M5 3h4l2 5-2.5 1.5a11 11 0 0 0 6 6L16 13l5 2v4a2 2 0 0 1-2 2A16 16 0 0 1 3 5a2 2 0 0 1 2-2"/></svg>
          (253) 617-4930
        </li>
        <li>
          <svg viewBox="0 0 24 24" fill="none" stroke="#fff" stroke-width="2.2" stroke-linejoin="round"><rect x="2" y="5" width="20" height="14"/><path d="M2 5l10 8 10-8"/></svg>
          martin@plumlinegroup.com
        </li>
        <li>
          <svg viewBox="0 0 24 24" fill="none" stroke="#fff" stroke-width="2"><circle cx="12" cy="12" r="10"/><ellipse cx="12" cy="12" rx="4.5" ry="10"/><path d="M2 12h20M4 7h16M4 17h16"/></svg>
          www.varkoworks.com
        </li>
      </ul>
    </div>

    <div class="address-band">18761 52nd Avenue S, Ridgeford, NV 98047</div>
    <div class="edge-strip"><span></span><span></span></div>
  </section>

</body>
</html>
```